Business Card Design - Amberfield Court

We are looking at a new design for our business cards that has a modern and professional look. We run a residential aged care facility focussing on the care of residents. The cards will be used for potential clients, consultants and business opportunities in this sector. Blue and white is our main colours and would to see these colours incorporated in the design.
Industry/Entity Type
Business
Contact Information for Business Card
Amberfield Court, Darren Walsh, dwalsh@amberfieldcourt.com.au, Finance Manager, 0472 639 208, BCom, 37 Marrabel Crescent, Brindle Vale, Qld 4093.
Look and feel
Each slider illustrates characteristics of the customer's brand and the style your logo design should communicate.

```html
<!DOCTYPE html>
<html lang="en">
<head>
<meta charset="utf-8">
<title>Amberfield Court – Business Card</title>
<link rel="stylesheet" href="https://fonts.googleapis.com/css2?family=Open+Sans:wght@400;600;700&display=swap">
<style>
  :root {
    --page-bg: #e7e8ea;
    --card-white: #ffffff;
    --brand-blue: #4b7894;
    --brand-blue-deep: #35607a;
    --brand-blue-light: #6a93ab;
    --taupe: #a99c94;
    --text-grey: #4f5256;
    --rule-grey: #b9bcbf;
  }
  * { box-sizing: border-box; margin: 0; padding: 0; }
  html, body {
    width: 1200px; height: 950px; overflow: hidden;
    background: var(--page-bg);
    font-family: "Open Sans", Arial, sans-serif;
  }
  .stage {
    width: 1200px; height: 950px;
    display: flex; flex-direction: column; align-items: center; justify-content: center;
    gap: 50px;
  }
  .card {
    width: 700px; height: 400px; position: relative;
    box-shadow: 0 8px 24px rgba(0,0,0,0.18);
  }
  /* front */
  .card-front { background: var(--card-white); }
  .brand {
    position: absolute; top: 82px; left: 0; width: 100%;
    display: flex; align-items: center; justify-content: center; gap: 16px;
    padding-left: 70px;
  }
  .brand-dot {
    width: 54px; height: 54px; border-radius: 50%;
    background: var(--brand-blue);
  }
  .brand-name {
    font-size: 30px; font-weight: 600; color: var(--brand-blue);
    letter-spacing: 1px;
  }
  .details {
    position: absolute; top: 222px; left: 0; width: 100%;
    display: flex; justify-content: center;
  }
  .person {
    text-align: right; padding-right: 18px; padding-top: 4px;
  }
  .person-name { font-size: 22px; font-weight: 700; color: var(--brand-blue); line-height: 1.2; }
  .person-name .credential { font-weight: 600; }
  .person-role { font-size: 17px; color: var(--taupe); line-height: 1.3; }
  .person-email { font-size: 16px; color: var(--text-grey); line-height: 1.4; }
  .divider { width: 1px; background: var(--rule-grey); height: 118px; }
  .contact {
    padding-left: 18px; padding-top: 4px;
    font-size: 17px; color: var(--text-grey); line-height: 1.35;
  }
  .contact-line { display: flex; align-items: center; gap: 9px; }
  .contact-line svg { width: 15px; height: 15px; flex: none; }
  .address { margin-bottom: 4px; }
  /* back */
  .card-back {
    background: linear-gradient(120deg, var(--brand-blue-deep) 0%, var(--brand-blue) 60%, var(--brand-blue-light) 100%);
  }
  .back-brand {
    position: absolute; top: 140px; left: 0; width: 100%;
    display: flex; align-items: center; justify-content: center; gap: 18px;
  }
  .back-dot { width: 64px; height: 64px; border-radius: 50%; background: var(--card-white); }
  .back-name { font-size: 36px; font-weight: 600; color: var(--card-white); letter-spacing: 1px; }
  .back-web {
    position: absolute; top: 240px; left: 0; width: 100%; text-align: center;
    font-size: 20px; color: var(--card-white); letter-spacing: 1px;
  }
</style>
</head>
<body>
<main class="stage">
  <section class="card card-front" aria-label="Business card front">
    <div class="brand">
      <span class="brand-dot"></span>
      <span class="brand-name">Amberfield Court</span>
    </div>
    <div class="details">
      <div class="person">
        <p class="person-name">Darren Walsh <span class="credential">BCom</span></p>
        <p class="person-role">Finance Manager</p>
        <p class="person-email">dwalsh@amberfieldcourt.com.au</p>
      </div>
      <div class="divider"></div>
      <div class="contact">
        <p class="address">37 Marrabel Crescent<br>Brindle Vale, Qld 4093.</p>
        <p class="contact-line">
          <svg viewBox="0 0 16 16" aria-hidden="true"><path fill="#35607a" d="M3.6 1.5 6 1l1.3 3.3-1.6 1.2a8 8 0 0 0 4.8 4.8l1.2-1.6 3.3 1.3-.5 2.4c-.2.6-.8 1-1.4.9C7.3 12.6 3.4 8.7 2.7 2.9c-.1-.6.3-1.2.9-1.4z"/></svg>
          <span>0472 639 208</span>
        </p>
        <p class="contact-line">
          <svg viewBox="0 0 16 16" aria-hidden="true"><circle cx="8" cy="8" r="7" fill="#35607a"/><path d="M1.5 8h13M8 1c2.2 2 2.2 12 0 14M8 1c-2.2 2-2.2 12 0 14" stroke="#fff" stroke-width="1" fill="none"/></svg>
          <span>www.amberfieldcourt.com.au</span>
        </p>
      </div>
    </div>
  </section>

  <section class="card card-back" aria-label="Business card back">
    <div class="back-brand">
      <span class="back-dot"></span>
      <span class="back-name">Amberfield Court</span>
    </div>
    <p class="back-web">amberfieldcourt.com.au</p>
  </section>
</main>
</body>
</html>
```